Brightway Haul & Upkeep Services, are a company that offers a 'one stop shop' pre-move clean up a

I have already selected a logo which I would like on the front of the business cards along with phone numbers, web address and email which are:
0487650392
www.brightwayhaul.com.au
brightwayhaulandupkeep@mailbox.example

On the back of the card I would like to list some of the types of service we offer (clean - move - repairs/maintenance) which are:
CLEAN - windows, gutters, solar panels, driveways/paths, carpets.
MOVE - Small/medium size house/office moves, large item pick-up & delivery, yard clean-up and removal.
General maintenance and repairs.

I would like the blue logo on a gray background.

Thanks

```html
<!DOCTYPE html>
<html lang="en">
<head>
<meta charset="utf-8">
<title>Brightway Haul &amp; Upkeep Services – Business Cards</title>
<link rel="stylesheet" href="https://fonts.googleapis.com/css2?family=Open+Sans:wght@400;600;700&display=swap">
<style>
  :root {
    --page-bg: #e9e9e9;
    --card-grey-light: #d9d9db;
    --card-grey: #c4c5c7;
    --brand-blue: #2a74c0;
    --ink: #1f1f1f;
    --swoosh-dark: #1c1c1c;
  }
  * { margin: 0; padding: 0; box-sizing: border-box; }
  html, body {
    width: 1200px; height: 381px; overflow: hidden;
    background: var(--page-bg);
    font-family: "Open Sans", Arial, sans-serif;
    color: var(--ink);
  }
  .canvas { position: relative; width: 1200px; height: 381px; }

  .card {
    position: absolute; top: 37px;
    width: 542px; height: 308px;
    border-radius: 28px; overflow: hidden;
    background: linear-gradient(135deg, var(--card-grey-light), var(--card-grey));
    box-shadow: 0 2px 6px rgba(0,0,0,.18);
  }
  .card--front { left: 52px; }
  .card--back { left: 619px; }

  .brand-name {
    position: absolute;
    color: var(--brand-blue);
    font-weight: 700;
    line-height: 1.05;
    text-transform: uppercase;
  }
  .brand-name .line-main { display: block; font-size: 36px; letter-spacing: .5px; }
  .brand-name .line-sub { display: block; font-size: 19px; letter-spacing: .4px; margin-top: 6px; }
  .card--front .brand-name { left: 0; right: 0; top: 92px; text-align: center; }
  .card--back .brand-name { left: 24px; top: 92px; }

  .contact-list {
    position: absolute; left: 0; right: 0; top: 165px;
    list-style: none; text-align: center;
    font-size: 14.5px; line-height: 24.5px;
  }
  .contact-list li { display: flex; justify-content: center; align-items: center; gap: 6px; }
  .contact-icon { width: 12px; height: 12px; fill: var(--brand-blue); }

  .swoosh { position: absolute; left: 0; bottom: 0; width: 542px; height: 90px; }

  .services-title {
    position: absolute; left: 23px; top: 158px;
    color: var(--brand-blue); font-size: 21px; font-weight: 600; letter-spacing: 1.6px;
  }
  .service-row {
    position: absolute; left: 22px; display: flex; gap: 10px;
    font-size: 13.5px; line-height: 20px;
  }
  .service-row .label { color: var(--brand-blue); font-weight: 600; font-size: 15px; width: 58px; flex: none; }
  .service-row--clean { top: 196px; }
  .service-row--move { top: 225px; width: 470px; }
  .general-note {
    position: absolute; left: 23px; top: 277px;
    color: var(--brand-blue); font-size: 15px; font-weight: 600; letter-spacing: 1.1px;
  }
</style>
</head>
<body>
<div class="canvas">

  <section class="card card--front">
    <div class="brand-name">
      <span class="line-main">Brightway Haul</span>
      <span class="line-sub">&amp; Upkeep Services</span>
    </div>
    <ul class="contact-list">
      <li>
        <svg class="contact-icon" viewBox="0 0 12 12" aria-hidden="true"><path d="M2.5 1 L4.5 1 L5.2 3.5 L4 4.5 Q5 7 7.5 8 L8.5 6.8 L11 7.5 L11 9.5 Q10 11 8 10.8 Q2 9.5 1 3.5 Q1 1.8 2.5 1Z"/></svg>
        0487650392
      </li>
      <li>
        <svg class="contact-icon" viewBox="0 0 12 12" aria-hidden="true"><circle cx="6" cy="6" r="5.5"/><path d="M0.8 6 H11.2 M6 0.5 V11.5 M2 3 H10 M2 9 H10" stroke="#d0d0d2" stroke-width=".8" fill="none"/></svg>
        www.brightwayhaul.com.au
      </li>
      <li>
        <svg class="contact-icon" viewBox="0 0 12 12" aria-hidden="true"><rect x="0.5" y="2.5" width="11" height="7.5" rx="1"/><path d="M0.8 3 L6 7 L11.2 3" stroke="#d0d0d2" stroke-width=".9" fill="none"/></svg>
        brightwayhaulandupkeep@mailbox.example
      </li>
    </ul>
    <svg class="swoosh" viewBox="0 0 542 90" preserveAspectRatio="none" aria-hidden="true">
      <path d="M0 30 Q120 10 260 30 Q400 52 542 22 L542 90 L0 90Z" fill="var(--swoosh-dark)"/>
      <path d="M0 50 Q150 28 300 48 Q420 62 542 42 L542 90 L0 90Z" fill="#e4e4e6"/>
      <path d="M0 62 Q160 42 320 62 Q440 74 542 56 L542 90 L0 90Z" fill="var(--brand-blue)"/>
    </svg>
  </section>

  <section class="card card--back">
    <div class="brand-name">
      <span class="line-main">Brightway Haul</span>
      <span class="line-sub">&amp; Upkeep Services</span>
    </div>
    <h2 class="services-title">Services we offer</h2>
    <div class="service-row service-row--clean">
      <span class="label">CLEAN:</span>
      <span>Windows, Gutters, Solar Panels, Driveways/paths, Carpets.</span>
    </div>
    <div class="service-row service-row--move">
      <span class="label">MOVE:</span>
      <span>Small/medium Size House/office Moves, Large Item Pick-up &amp; Delivery, Yard Clean-up And Removal.</span>
    </div>
    <p class="general-note">General maintenance and repairs.</p>
  </section>

</div>
</body>
</html>
```